Zolvana Stationary and Branding Documents

Corporate Identity Branding stationary needed for IT Recruiting Firm.

I already have a Logo, business cards and website. I need to get designs completed for the remaining corporate identity documents.

The documentation should use similar colors as my website and business card. The designs should modern and clean.

http://zolvanaworks.example/

Target Market(s)

Information Technology Industry

Industry/Entity Type

Information Technology

Colors
3377b5
0255a3
fbee3e
f78f20
f37122
33a6d7
000000
0592cd

Requirements
Must have
• Letter Head
• Folder Design
• PowerPoint Design
• Invoice
• Envelope
Nice to have
• Proposal
• Flyer
• Brochure
Should not have
• Logo
• Business Cards
• Website

```html
<!DOCTYPE html>
<html lang="en">
<head>
<meta charset="utf-8">
<title>Zolvana Letterhead</title>
<link href="https://fonts.googleapis.com/css2?family=Open+Sans:wght@400;600;700&display=swap" rel="stylesheet">
<style>
  :root {
    --brand-blue: #0255a3;
    --brand-orange: #f37122;
    --ink-grey: #5a5f66;
    --paper: #f7f8f9;
    --backdrop: #dfe4ef;
  }
  * { margin: 0; padding: 0; box-sizing: border-box; }
  html, body {
    width: 1200px; height: 784px; overflow: hidden;
    background: var(--backdrop);
    font-family: "Open Sans", sans-serif;
  }
  .letterhead {
    position: absolute; left: 338px; top: 22px;
    width: 523px; height: 740px;
    background: var(--paper);
    box-shadow: 0 2px 10px rgba(40, 60, 110, 0.18);
  }
  .letterhead-header {
    position: absolute; left: 40px; right: 36px; top: 34px;
    display: flex; align-items: flex-end; gap: 12px;
  }
  .brand-name {
    font-size: 30px; font-weight: 600; color: var(--brand-blue);
    line-height: 1; letter-spacing: 0.5px;
  }
  .header-rule {
    flex: 1; height: 1px; background: var(--brand-blue);
    margin-bottom: 4px;
  }
  .contact-block {
    text-align: left; font-size: 6.5px; line-height: 1.5;
    border-bottom: 1px solid var(--brand-blue); padding-bottom: 2px;
  }
  .contact-address { color: var(--brand-orange); font-weight: 700; font-size: 7px; }
  .contact-lines { color: var(--ink-grey); display: flex; gap: 8px; }
  .contact-item { display: inline-flex; align-items: center; gap: 3px; }
  .contact-item svg { width: 6px; height: 6px; fill: var(--brand-blue); }
  .letterhead-footer {
    position: absolute; left: 40px; right: 36px; bottom: 40px;
    display: flex; align-items: center; gap: 10px;
  }
  .footer-web { font-size: 7px; color: var(--ink-grey); white-space: nowrap; }
  .footer-rule { flex: 1; height: 1px; background: var(--brand-orange); }
</style>
</head>
<body>
  <main class="letterhead">
    <header class="letterhead-header">
      <div class="brand-name">Zolvana</div>
      <div class="header-rule"></div>
      <div class="contact-block">
        <div class="contact-address">Two Harbor Plaza 410, 9th Avenue W</div>
        <div class="contact-lines">
          <span class="contact-item">
            <svg viewBox="0 0 10 10"><rect width="10" height="10" rx="2"/></svg>5550142290
          </span>
          <span class="contact-item">
            <svg viewBox="0 0 10 10"><rect width="10" height="10" rx="2"/></svg>info@zolvanaworks.example
          </span>
        </div>
      </div>
    </header>
    <footer class="letterhead-footer">
      <span class="footer-web">www.zolvanaworks.example</span>
      <div class="footer-rule"></div>
    </footer>
  </main>
</body>
</html>
```